Health Coaching website focused on diabetes management using Vantelo template

I am starting a health coaching business and would like to use Plumestack and an Vantelo template. The coaching will focus on Pre-diabetic and chronic disease patients so it will need to have a personal as well as a slight clinical look to it. The site should have an overall look similar to Meadow Loop theme. I will purchase the Vantelo designer package for use.

Target Market(s)

40-60 year olds with pre-diabetes or concerned about chronic disease, maintaining health, nutrition and weight loss

Industry/Entity Type

Health And Wellness

Number of Pages Required

5+ page

Colors
87cfc6
60b9df
fee18a
00a990
3276b5

Requirements
Must have
• It should contain an ecommerce tab, member's only area, interactive blog, built-in SEO and an opt-in area on every page. It should have several call to actions throughout the site. The site should have an overall look similar to Meadow Loop theme. Hosting on Servunda. Also needed all the essential plumestack plugins:
• Keystep forms & Keystep entry pages
• Pondra Metrics
• Vantelo shield plus
• Postwren
• Valdeno
• Vault Parrot
• Kindle SEO
• Drifting Share Strip
• Q7 Rapid Store
• Tembi
Nice to have
• Ecommerce ready with cartoflex plugin
• Hi-res pictures of people in my demographic enjoying life and/or exercising, cooking, etc.
Should not have
• slider on homepage
• my profile on homepage

```html
<!DOCTYPE html>
<html lang="en">
<head>
<meta charset="utf-8">
<title>Vitalroot Coaching – Testimonials</title>
<link rel="stylesheet" href="https://fonts.googleapis.com/css2?family=Jost:wght@400;500&family=Open+Sans:wght@400;600;700&display=swap">
<style>
:root{
  --teal:#00a990;
  --blue:#3276b5;
  --blue-light:#5f9fd6;
  --ink:#222;
  --text:#444;
  --muted:#777;
  --line:#e2e2e2;
  --band:#e8e8e8;
  --footer:#1f232d;
  --footer-text:#b9bdc6;
  --cream:#f1efe6;
}
*{box-sizing:border-box;margin:0;padding:0}
html,body{width:667px;height:1200px;overflow:hidden}
body{position:relative;background:#fff;font-family:"Open Sans",Arial,sans-serif;color:var(--text)}
.wrap{position:absolute;left:90px;width:488px}

/* header */
.site-header{position:absolute;top:0;left:0;width:667px;height:62px}
.brand{position:absolute;left:90px;top:12px;display:flex;align-items:center;gap:8px}
.brand-dot{width:30px;height:30px;border-radius:50%;background:var(--teal)}
.brand-name{font-family:"Jost",sans-serif;font-size:17px;line-height:19px;color:var(--ink);font-weight:400}
.header-phone{position:absolute;left:348px;top:23px;display:flex;align-items:center;gap:8px;font-size:12px;color:#333}
.icon-round{width:19px;height:19px;border-radius:50%;background:var(--teal);display:flex;align-items:center;justify-content:center}
.cta{position:absolute;left:457px;top:22px;width:121px;height:21px;background:var(--teal);color:#fff;font-size:7.5px;display:flex;align-items:center;justify-content:center;gap:6px;border-radius:2px;letter-spacing:.2px}

/* nav */
.main-nav{position:absolute;top:62px;left:0;width:667px;height:21px;background:var(--blue)}
.main-nav ul{position:absolute;left:90px;display:flex;list-style:none;height:21px}
.main-nav li{font-size:6.6px;font-weight:700;color:#fff;padding:0 8.5px;line-height:21px;border-right:1px solid rgba(255,255,255,.18)}
.main-nav li:first-child{border-left:1px solid rgba(255,255,255,.18)}
.main-nav li.active{background:var(--teal)}

/* hero */
.hero{position:absolute;top:83px;left:0;width:667px;height:188px;background:var(--cream)}
.hero-photo{position:absolute;left:0;top:0;width:380px;height:188px;background:linear-gradient(100deg,#6d4a35 0%,#a7794f 35%,#cdb493 70%,#e7dfcd 100%)}
.hero-copy{position:absolute;left:380px;width:200px;top:36px;text-align:center}
.hero-title{font-family:"Jost",sans-serif;font-size:27px;line-height:34px;color:#111}
.hero-sub{font-size:10px;line-height:12.5px;color:#222;margin-top:4px}
.dots{display:flex;justify-content:center;gap:4px;margin-top:17px}
.dots span{width:6px;height:6px;border-radius:50%;background:#777}
.dots span.on{background:var(--teal)}

.crumbs{position:absolute;top:271px;left:0;width:667px;height:21px;background:var(--band);font-size:7px;line-height:21px}
.crumbs p{position:absolute;left:90px;color:#444}
.crumbs b{color:#222}

/* title */
.section-title{position:absolute;top:313px;left:0;width:667px;text-align:center;font-family:"Jost",sans-serif;font-size:17px;color:#222}
.section-title span{color:var(--blue)}
.title-rule{position:absolute;top:348px;left:203px;width:261px;height:1px;background:#bbb}
.title-mark{position:absolute;top:341px;left:326px;width:15px;height:15px;border-radius:50%;background:#fff;border:1px solid #bbb}

/* testimonials */
.testimonials{position:absolute;top:375px;left:90px;width:488px}
.testimonial{position:relative;height:105px;border-bottom:1px solid var(--line)}
.avatar{position:absolute;left:2px;top:8px;width:51px;height:51px;border-radius:50%;border:2px solid var(--teal);background:radial-gradient(circle at 50% 40%,#e9d4b8,#c9a57c 70%,#9a7c5c)}
.avatar::after{content:"";position:absolute;left:12px;bottom:-7px;border-left:5px solid transparent;border-right:5px solid transparent;border-top:7px solid var(--teal)}
.quote{position:absolute;left:58px;top:5px;width:430px;font-size:7.1px;line-height:10.6px;color:#333}
.q{color:#a9c4e0;font-family:Georgia,serif;font-weight:700;font-size:11px;line-height:0}
.meta{position:absolute;left:61px;top:80px;width:427px;font-size:6.6px;color:#444;display:flex}
.meta .who{width:80px}
.meta .handle{color:var(--blue)}
.meta .when{margin-left:auto;color:#666;display:flex;gap:14px}
.meta-rule{position:absolute;left:58px;top:73px;width:160px;height:1px;background:var(--line)}

/* footer */
.site-footer{position:absolute;top:1019px;left:0;width:667px;height:156px;background:var(--footer)}
.col{position:absolute;top:24px}
.col h4{font-family:"Jost",sans-serif;font-weight:400;font-size:10.5px;color:#fff;padding-bottom:7px;border-bottom:1px solid #3a3f4b}
.col h4 span{color:var(--teal)}
.links{list-style:none;margin-top:7px}
.links li{font-size:6.8px;color:var(--footer-text);line-height:11.3px}
.links li::before{content:"›";margin-right:4px;color:#888}
.links li.on{color:var(--teal)}
.contact p{font-size:6.8px;color:var(--footer-text);line-height:10.5px}
.contact .org{color:#fff;font-weight:600;margin-top:8px}
.contact .line{display:flex;align-items:center;gap:5px;margin-top:7px;color:#fff;font-size:9px}
.contact .line.small{font-size:7px;color:var(--footer-text)}
.social{list-style:none;margin-top:9px}
.social li{display:flex;align-items:center;gap:6px;font-size:7px;color:var(--footer-text);height:22px}
.social i{width:17px;height:17px;border-radius:50%;background:#355c9a;border:1px solid #fff;display:block}
.foot-mark{position:absolute;left:470px;top:52px;width:110px;text-align:center;font-family:"Jost",sans-serif;font-size:15px;color:#7d828c}
.foot-mark i{display:block;width:30px;height:30px;border-radius:50%;background:#5b606a;margin:0 auto 8px}
.legal{position:absolute;top:1175px;left:0;width:667px;height:25px;background:var(--teal);font-size:6.8px;color:#fff;line-height:25px}
.legal p{position:absolute;left:90px}
</style>
</head>
<body>

<header class="site-header">
  <div class="brand"><span class="brand-dot"></span><span class="brand-name">Vitalroot<br>Coaching</span></div>
  <div class="header-phone">
    <span class="icon-round"><svg width="9" height="9" viewBox="0 0 24 24"><path fill="#fff" d="M6.6 10.8a15 15 0 0 0 6.6 6.6l2.2-2.2c.3-.3.7-.4 1-.2 1.1.4 2.3.6 3.6.6.6 0 1 .4 1 1V20c0 .6-.4 1-1 1A17 17 0 0 1 3 4c0-.6.4-1 1-1h3.5c.6 0 1 .4 1 1 0 1.3.2 2.5.6 3.6.1.3 0 .7-.2 1z"/></svg></span>
    555-014-2290
  </div>
  <a class="cta"><svg width="8" height="8" viewBox="0 0 10 10"><rect x="1" y="2" width="8" height="7" fill="none" stroke="#fff"/><path d="M1 4h8M3 1v2M7 1v2" stroke="#fff"/></svg>MAKE AN APPOINTMENT</a>
</header>

<nav class="main-nav">
  <ul>
    <li>HOME</li><li>ABOUT VITALROOT</li><li>OUR COURSES</li><li>SPECIAL OFFERS</li><li class="active">TESTIMONIALS</li><li>BLOG</li><li>FAQ'S</li><li>CONTACT US</li>
  </ul>
</nav>

<section class="hero">
  <div class="hero-photo" role="img" aria-label="Photo of a smiling couple cooking fresh vegetables together in a warm home kitchen"></div>
  <div class="hero-copy">
    <h1 class="hero-title">Vitalroot<br>Coaching</h1>
    <p class="hero-sub">Get the health and lifestyle<br>you want now!</p>
    <div class="dots"><span class="on"></span><span></span><span></span><span></span></div>
  </div>
</section>

<div class="crumbs"><p>Home / <b>Testimonials</b></p></div>

<h2 class="section-title">Client <span>Testimonials</span></h2>
<div class="title-rule"></div><div class="title-mark"></div>

<main class="testimonials">
  <article class="testimonial">
    <div class="avatar" role="img" aria-label="Client portrait"></div>
    <p class="quote"><span class="q">“</span> Lorem ipsum dolor smit amet, consectetuer adipiscing elitmk, sed amet diam nonummy nibh euismod tincidun ntl more utmn laoreetml dolore magna aliquam erat volutpat. Ut wisi enim ad minim veniam, quis nostrud exer tationk ullamcorik Lorem ipsum dolor smit amet, consectetuer adipiscing elitmk, sed amet diam nonummy nibh euismod tincidun ntl more utmn laoreetml dolore magna aliquam erat volutpat. Ut wisi enim ad minim veniam, quis nostrud exer tationk ullamcorik &nbsp; Lorem ipsum dolor smit amet, consectetuer adipiscing elitmk, <span class="q">”</span></p>
    <div class="meta-rule"></div>
    <div class="meta"><span class="who">- Mrs. Sunfrak Hloko</span><span class="handle">@shloko</span><span class="when"><span>▦ 09 Nov 2016</span><span>◷ 5.15 PM</span></span></div>
  </article>
  <article class="testimonial">
    <div class="avatar" role="img" aria-label="Client portrait"></div>
    <p class="quote"><span class="q">“</span> Lorem ipsum dolor smit amet, consectetuer adipiscing elitmk, sed amet diam nonummy nibh euismod tincidun ntl more utmn laoreetml dolore magna aliquam erat volutpat. Ut wisi enim ad minim veniam, quis nostrud exer tationk ullamcorik Lorem ipsum dolor smit amet, consectetuer adipiscing elitmk, sed amet diam nonummy nibh euismod tincidun ntl more utmn laoreetml dolore magna aliquam erat volutpat. Ut wisi enim ad minim veniam, quis nostrud exer tationk ullamcorik &nbsp; Lorem ipsum dolor smit amet, consectetuer adipiscing elitmk, <span class="q">”</span></p>
    <div class="meta-rule"></div>
    <div class="meta"><span class="who" style="width:84px">- Mrs. Euismod tincidun</span><span class="handle">@shloko</span><span class="when"><span>▦ 09 Nov 2016</span><span>◷ 5.15 PM</span></span></div>
  </article>
  <article class="testimonial">
    <div class="avatar" role="img" aria-label="Client portrait"></div>
    <p class="quote"><span class="q">“</span> Lorem ipsum dolor smit amet, consectetuer adipiscing elitmk, sed amet diam nonummy nibh euismod tincidun ntl more utmn laoreetml dolore magna aliquam erat volutpat. Ut wisi enim ad minim veniam, quis nostrud exer tationk ullamcorik Lorem ipsum dolor smit amet, consectetuer adipiscing elitmk, sed amet diam nonummy nibh euismod tincidun ntl more utmn laoreetml dolore magna aliquam erat volutpat. Ut wisi enim ad minim veniam, quis nostrud exer tationk ullamcorik &nbsp; Lorem ipsum dolor smit amet, consectetuer adipiscing elitmk, <span class="q">”</span></p>
    <div class="meta-rule"></div>
    <div class="meta"><span class="who">- Mrs. Sunfrak Hloko</span><span class="handle">@shloko</span><span class="when"><span>▦ 09 Nov 2016</span><span>◷ 5.15 PM</span></span></div>
  </article>
  <article class="testimonial">
    <div class="avatar" role="img" aria-label="Client portrait"></div>
    <p class="quote"><span class="q">“</span> Lorem ipsum dolor smit amet, consectetuer adipiscing elitmk, sed amet diam nonummy nibh euismod tincidun ntl more utmn laoreetml dolore magna aliquam erat volutpat. Ut wisi enim ad minim veniam, quis nostrud exer tationk ullamcorik Lorem ipsum dolor smit amet, consectetuer adipiscing elitmk, sed amet diam nonummy nibh euismod tincidun ntl more utmn laoreetml dolore magna aliquam erat volutpat. Ut wisi enim ad minim veniam, quis nostrud exer tationk ullamcorik &nbsp; Lorem ipsum dolor smit amet, consectetuer adipiscing elitmk, <span class="q">”</span></p>
    <div class="meta-rule"></div>
    <div class="meta"><span class="who" style="width:84px">- Mrs. Euismod tincidun</span><span class="handle">@shloko</span><span class="when"><span>▦ 09 Nov 2016</span><span>◷ 5.15 PM</span></span></div>
  </article>
  <article class="testimonial">
    <div class="avatar" role="img" aria-label="Client portrait"></div>
    <p class="quote"><span class="q">“</span> Lorem ipsum dolor smit amet, consectetuer adipiscing elitmk, sed amet diam nonummy nibh euismod tincidun ntl more utmn laoreetml dolore magna aliquam erat volutpat. Ut wisi enim ad minim veniam, quis nostrud exer tationk ullamcorik Lorem ipsum dolor smit amet, consectetuer adipiscing elitmk, sed amet diam nonummy nibh euismod tincidun ntl more utmn laoreetml dolore magna aliquam erat volutpat. Ut wisi enim ad minim veniam, quis nostrud exer tationk ullamcorik &nbsp; Lorem ipsum dolor smit amet, consectetuer adipiscing elitmk, <span class="q">”</span></p>
    <div class="meta-rule"></div>
    <div class="meta"><span class="who">- Mrs. Sunfrak Hloko</span><span class="handle">@shloko</span><span class="when"><span>▦ 09 Nov 2016</span><span>◷ 5.15 PM</span></span></div>
  </article>
  <article class="testimonial">
    <div class="avatar" role="img" aria-label="Client portrait"></div>
    <p class="quote"><span class="q">“</span> Lorem ipsum dolor smit amet, consectetuer adipiscing elitmk, sed amet diam nonummy nibh euismod tincidun ntl more utmn laoreetml dolore magna aliquam erat volutpat. Ut wisi enim ad minim veniam, quis nostrud exer tationk ullamcorik Lorem ipsum dolor smit amet, consectetuer adipiscing elitmk, sed amet diam nonummy nibh euismod tincidun ntl more utmn laoreetml dolore magna aliquam erat volutpat. Ut wisi enim ad minim veniam, quis nostrud exer tationk ullamcorik &nbsp; Lorem ipsum dolor smit amet, consectetuer adipiscing elitmk, <span class="q">”</span></p>
    <div class="meta-rule"></div>
    <div class="meta"><span class="who" style="width:84px">- Mrs. Euismod tincidun</span><span class="handle">@shloko</span><span class="when"><span>▦ 09 Nov 2016</span><span>◷ 5.15 PM</span></span></div>
  </article>
</main>

<footer class="site-footer">
  <div class="col" style="left:90px;width:67px">
    <h4>QUICK <span>LINKS</span></h4>
    <ul class="links">
      <li class="on">Home</li><li>About Vitalroot</li><li>Our Courses</li><li>Special Offers</li><li>Testimonials</li><li>Blog</li><li>Faq's</li><li>Contact Us</li>
    </ul>
  </div>
  <div class="col contact" style="left:181px;width:110px">
    <h4>CONTACT <span>DETAILS</span></h4>
    <p class="org">VITALROOT COACHING</p>
    <p>123, Lorem Ipsum Dollar Smit Amet,<br>Nibh Nonumy. Golham - 123 456</p>
    <p class="line"><svg width="8" height="8" viewBox="0 0 24 24"><path fill="#00a990" d="M6.6 10.8a15 15 0 0 0 6.6 6.6l2.2-2.2c.3-.3.7-.4 1-.2 1.1.4 2.3.6 3.6.6.6 0 1 .4 1 1V20c0 .6-.4 1-1 1A17 17 0 0 1 3 4c0-.6.4-1 1-1h3.5c.6 0 1 .4 1 1 0 1.3.2 2.5.6 3.6.1.3 0 .7-.2 1z"/></svg>555-014-2290</p>
    <p class="line"><svg width="9" height="8" viewBox="0 0 10 9"><rect x="2" y="0" width="6" height="3" fill="none" stroke="#00a990"/><rect x="0" y="3" width="10" height="4" fill="#00a990"/><rect x="2" y="6" width="6" height="3" fill="#1f232d" stroke="#00a990"/></svg>555-014-7731</p>
    <p class="line small"><svg width="8" height="6" viewBox="0 0 10 7"><rect width="10" height="7" fill="#00a990"/><path d="M0 0l5 4 5-4" stroke="#1f232d" fill="none"/></svg>hello@vitalroot-coach.com</p>
  </div>
  <div class="col" style="left:315px;width:125px">
    <h4>FOLLOW <span>US</span></h4>
    <ul class="social">
      <li><i></i>Friendline</li><li><i style="background:#3d9fd6"></i>Chirpfeed</li><li><i style="background:#1a6aa0"></i>Linkpro</li><li><i style="background:#c9302c"></i>Circleplus</li>
    </ul>
  </div>
  <div class="foot-mark"><i></i>Vitalroot Coaching</div>
</footer>
<div class="legal"><p>© 2016 Vitalroot Coaching. All Rights Reserved.</p></div>

</body>
</html>
```